Carpentry framing business card and logo design

We need a logo that works well with baseball caps, tee shirts and sweat shirts. We are a carpentry framing company specializing in apartment complexes and large residential communities. We work in what is known as the tri state area southeastern Pennsylvania , New Jersey and northern Delaware . We would like to see die signs using the old English letter M and royal blue colors. Also we stress OSHA compliance and safety.

Industry/Entity Type

Residential

Contact Information for Business Card

Valdrick Construction Co Inc
4870 Quillford Lane
Ambler PA 19087
Dale Valdrick
dale1valdrick@norvexmail.com
267-815-0926

```html
<!DOCTYPE html>
<html lang="en">
<head>
<meta charset="utf-8">
<title>Valdrick Construction Co Inc — Business Card</title>
<link href="https://fonts.googleapis.com/css2?family=Cinzel:wght@400;500&family=Arimo:wght@400&display=swap" rel="stylesheet">
<style>
  :root {
    --backdrop: #e9e6e1;
    --card: #ffffff;
    --royal: #3a3396;
    --coral: #e8684f;
    --rule: #4a43a3;
  }
  * { box-sizing: border-box; margin: 0; padding: 0; }
  html, body { width: 1200px; height: 818px; overflow: hidden; }
  body {
    background: var(--backdrop);
    display: flex;
    align-items: center;
    justify-content: center;
  }
  .business-card {
    position: relative;
    width: 860px;
    height: 500px;
    background: var(--card);
    box-shadow: 0 10px 30px rgba(0,0,0,0.15);
    overflow: hidden;
  }
  .company-mark {
    position: absolute;
    top: 92px;
    left: 0;
    right: 0;
    display: flex;
    align-items: center;
    justify-content: center;
    gap: 16px;
  }
  .company-mark__square {
    width: 26px;
    height: 26px;
    background: var(--royal);
  }
  .company-mark__name {
    font-family: "Cinzel", serif;
    font-weight: 500;
    font-size: 34px;
    letter-spacing: 1px;
    color: var(--royal);
  }
  .name-rule {
    position: absolute;
    top: 240px;
    left: 0;
    right: 0;
    display: flex;
    align-items: center;
    gap: 22px;
  }
  .name-rule__line {
    flex: 1;
    height: 2px;
    background: var(--rule);
  }
  .holder-name {
    font-family: "Cinzel", serif;
    font-weight: 400;
    font-size: 34px;
    color: var(--coral);
    letter-spacing: 1px;
    white-space: nowrap;
  }
  .contact-list {
    position: absolute;
    top: 300px;
    left: 0;
    right: 0;
    list-style: none;
    text-align: center;
    font-family: "Arimo", sans-serif;
    font-size: 24px;
    line-height: 42px;
    color: var(--royal);
  }
  .edge-band {
    position: absolute;
    left: 0;
    right: 0;
    bottom: 0;
    height: 30px;
    background: var(--royal);
  }
</style>
</head>
<body>
  <div class="business-card">
    <div class="company-mark">
      <span class="company-mark__square"></span>
      <span class="company-mark__name">Valdrick Construction Co Inc</span>
    </div>
    <div class="name-rule">
      <span class="name-rule__line"></span>
      <span class="holder-name">Dale Valdrick</span>
      <span class="name-rule__line"></span>
    </div>
    <ul class="contact-list">
      <li class="contact-phone">555-815-0926</li>
      <li class="contact-email">dale1valdrick@norvexmail.com</li>
      <li class="contact-address">4870 Quillford Lane Corvanth QX 40518</li>
    </ul>
    <div class="edge-band"></div>
  </div>
</body>
</html>
```